Professional looking Roller Blind Discount Card that portrays quality at a value for money price!

We need a double sided business card designed as a discount card. Size 90mm wide x 55mm high.We would like it to look professional and portray quality at a value for money price point.I have uploaded a word document with a basic layout with the information we want included on each side of the card. Please put your own thought into the layout.

Contact Information for Business Card

As per word document attached.

```html
<!DOCTYPE html>
<html lang="en">
<head>
<meta charset="utf-8">
<title>K&amp;L Interiors – Roller Blind Discount Card</title>
<link href="https://fonts.googleapis.com/css2?family=Oswald:wght@500;700&family=Montserrat:wght@300;400;600&display=swap" rel="stylesheet">
<style>
  :root {
    --bg: #d9dadc;
    --card: #ffffff;
    --blue: #29a3df;
    --grey: #5f6063;
    --grey-dark: #3e3f42;
    --photo-a: #c9b49a;
    --photo-b: #8f9a7c;
  }
  * { box-sizing: border-box; margin: 0; padding: 0; }
  html, body { width: 1200px; height: 896px; overflow: hidden; background: var(--bg); }
  body { position: relative; font-family: "Montserrat", sans-serif; }

  .card {
    position: absolute; top: 283px;
    width: 540px; height: 330px;
    background: var(--card);
    overflow: hidden;
    box-shadow: 0 6px 18px rgba(0,0,0,.18);
  }
  .card--front { left: 30px; }
  .card--back { left: 630px; }

  /* Front */
  .headline {
    position: absolute; left: 30px; top: 22px;
    font-family: "Oswald", sans-serif; font-weight: 700;
    font-size: 40px; letter-spacing: 1px; color: var(--blue); line-height: 1;
  }
  .offer-line {
    position: absolute; left: 30px; top: 72px;
    font-size: 24px; font-weight: 300; color: var(--grey); white-space: nowrap;
  }
  .offer-line strong { color: var(--blue); font-weight: 600; }
  .photos { position: absolute; left: 30px; top: 118px; display: flex; gap: 6px; }
  .photo { width: 122px; height: 100px; }
  .photo--play { background: linear-gradient(135deg, #e05a4a, #f2c33a 45%, #3fa34d 70%, #3a6fd0); }
  .photo--window { background: linear-gradient(160deg, var(--photo-a), var(--photo-b)); }
  .mark-square {
    position: absolute; left: 430px; top: 130px;
    width: 46px; height: 46px; background: var(--blue);
  }
  .brand {
    position: absolute; left: 30px; top: 228px;
    font-weight: 400; font-size: 44px; color: var(--blue); letter-spacing: 1px; white-space: nowrap;
  }
  .call-band {
    position: absolute; left: 0; right: 0; bottom: 0; height: 34px;
    background: var(--grey);
    color: #fff; font-size: 16px; font-weight: 400;
    display: flex; align-items: center; padding-left: 30px; gap: 6px;
  }
  .call-band .call-label { color: var(--blue); }

  /* Back */
  .top-band {
    position: absolute; left: 0; right: 0; top: 0; height: 40px;
    background: var(--blue); color: #fff;
    display: flex; align-items: center; justify-content: space-between;
    padding: 0 26px; font-size: 16px;
  }
  .back-square {
    position: absolute; left: 30px; top: 74px;
    width: 56px; height: 56px; background: var(--blue);
  }
  .guarantee-seal {
    position: absolute; left: 128px; top: 58px;
    width: 92px; height: 92px; border-radius: 50%;
    background: var(--grey);
  }
  .discount {
    position: absolute; left: 262px; top: 60px;
    font-family: "Oswald", sans-serif; font-weight: 700;
    font-size: 68px; color: var(--grey-dark); line-height: 1;
  }
  .services {
    position: absolute; left: 30px; top: 176px;
    font-family: "Oswald", sans-serif; font-weight: 500;
    font-size: 17px; color: var(--blue); white-space: nowrap;
  }
  .brand--back { top: 214px; font-size: 48px; }
  .bottom-accent {
    position: absolute; right: 0; bottom: 0; width: 170px; height: 14px;
    background: var(--blue);
  }
</style>
</head>
<body>

  <section class="card card--front" aria-label="Card front">
    <h1 class="headline">ROLLER BLINDS</h1>
    <p class="offer-line"><strong>FREE</strong> in Home Measure &amp; Quote</p>
    <div class="photos">
      <div class="photo photo--play" role="img" aria-label="Photo of a child playing in a colourful ball pit"></div>
      <div class="photo photo--window" role="img" aria-label="Photo of a room window fitted with a roller blind"></div>
    </div>
    <div class="mark-square" aria-hidden="true"></div>
    <p class="brand">K&amp;L INTERIORS</p>
    <div class="call-band"><span class="call-label">Call</span> <span>0400 123 456 Today</span></div>
  </section>

  <section class="card card--back" aria-label="Card back">
    <div class="top-band">
      <span>Call 0400 123 456 Today!</span>
      <span>Family Owned &amp; Operated</span>
    </div>
    <div class="back-square" aria-hidden="true"></div>
    <div class="guarantee-seal" role="img" aria-label="Best price guarantee seal"></div>
    <p class="discount">25% OFF</p>
    <p class="services">Quality Custom Made Roller Blinds Blockout – Screen – Light Filtering</p>
    <p class="brand brand--back">K&amp;L INTERIORS</p>
    <div class="bottom-accent" aria-hidden="true"></div>
  </section>

</body>
</html>
```